Business Cards for new orthopaedic surgery practice

My husband and I are starting our own orthopaedic surgery practice. We are looking for a business card that is uniform, but one will have my name/title and the other will have his. You can just create one design with my name on it for now. But when I choose your design as the winning design I will ask that you add another copy with his name/title.

We are looking for classy, simple, elite all in one. We like dark blues/a little gold/yellow. Something that goes with our logo. We want our logo incorporated. Here is all the info you need:
Business name: RV Bone & Vitality Center
Location: 38517 North Willowmere Ave
Maple Hollow, FL 34982
Phone: 954-218-4063
Fax: 954-582-7341
Email: info@myrvbonecare.example

Names: Lydia Vance, M.D.
Board Certified Hand and Upper Extremity Surgeon

Ebo Dansu, M.D.
Board Certified Hip & Knee Replacement/General Orthopaedic Surgeon

Can decide what you want to put on the back. Maybe a slogan:
Steady Hands. Centered on You

I am just going to upload our logo. The only thing is if we select you as the winning design, the location, and phone numbers may change. We will need your help to update that once fully solidified.

Industry/Entity Type

Medical

Contact Information for Business Card

Colors
0054AA
0677BA
7BADD7
CADEEF
E8F1F8
0094D4
00A9DD
6FCCEA
C7EBF8
E9F6FB

Requirements
Must have
• class, appeal,
Should not have
• We want to air on the side of masculine if we are looking at masculine vs. feminine feel. But we still want it classy, sophisticated, and something we will love

```html
<!DOCTYPE html>
<html lang="en">
<head>
<meta charset="utf-8">
<title>RV Bone &amp; Vitality Center — Business Card</title>
<link rel="stylesheet" href="https://fonts.googleapis.com/css2?family=Cinzel:wght@600&family=Arimo:wght@400&display=swap">
<style>
  :root {
    --backdrop: #e6e6e6;
    --card-white: #ffffff;
    --navy: #1f2d5a;
    --navy-top: #283b6b;
    --navy-bottom: #1b2852;
    --gold: #c9a263;
    --text-grey: #3c3c44;
    --mark-blue: #4a68b8;
  }
  * { box-sizing: border-box; margin: 0; padding: 0; }
  html, body {
    width: 1200px; height: 1200px; overflow: hidden;
    background: var(--backdrop);
  }
  .canvas { position: relative; width: 1200px; height: 1200px; }

  .card { position: absolute; width: 688px; height: 393px; }
  .card-front { left: 267px; top: 159px; background: var(--card-white); }
  .card-back {
    left: 262px; top: 653px;
    background: linear-gradient(to bottom, var(--navy-top), var(--navy-bottom));
  }

  .identity {
    position: absolute; right: 318px; top: 138px;
    text-align: right;
    font-family: "Arimo", Arial, sans-serif;
  }
  .doctor-name {
    font-family: "Cinzel", "Times New Roman", serif;
    font-weight: 600; font-size: 24px; letter-spacing: 0.3px;
    color: var(--navy); line-height: 1; margin-bottom: 6px;
    white-space: nowrap;
  }
  .doctor-title { color: var(--gold); font-size: 16px; line-height: 19px; }
  .address { color: var(--text-grey); font-size: 16.5px; line-height: 21px; margin-top: 5px; }

  .divider {
    position: absolute; left: 386px; top: 146px;
    width: 1.5px; height: 100px; background: var(--navy);
  }

  .contact-list {
    position: absolute; left: 400px; top: 154px; list-style: none;
    font-family: "Arimo", Arial, sans-serif; font-size: 16.5px;
    color: var(--text-grey);
  }
  .contact-list li { display: flex; align-items: center; height: 20.5px; }
  .contact-list svg { width: 14px; height: 14px; margin-right: 12px; fill: var(--navy); flex: none; }

  .practice-mark {
    position: absolute; left: 0; right: 0; top: 150px;
    display: flex; align-items: center; justify-content: center; gap: 14px;
  }
  .practice-mark .dot {
    width: 16px; height: 16px; border-radius: 50%; background: var(--mark-blue);
  }
  .practice-name {
    font-family: "Cinzel", "Times New Roman", serif; font-weight: 600;
    font-size: 26px; letter-spacing: 1px; color: var(--mark-blue);
  }

  .slogan {
    position: absolute; left: 0; right: 0; top: 335px; text-align: center;
    font-family: "Arimo", Arial, sans-serif; font-size: 16px;
    letter-spacing: 3.6px; color: var(--gold); padding-left: 8px;
  }
</style>
</head>
<body>
<div class="canvas">

  <section class="card card-front">
    <div class="identity">
      <h1 class="doctor-name">LYDIA VANCE, M.D.</h1>
      <p class="doctor-title">Board Certified Hand and<br>Upper Extremity Surgeon</p>
      <p class="address">38517 North Willowmere Ave<br>Maple Hollow, FL 34982</p>
    </div>
    <div class="divider"></div>
    <ul class="contact-list">
      <li>
        <svg viewBox="0 0 24 24" aria-hidden="true"><path d="M6.6 10.8a15.1 15.1 0 0 0 6.6 6.6l2.2-2.2c.3-.3.7-.4 1-.2 1.1.4 2.3.6 3.6.6.6 0 1 .4 1 1V20c0 .6-.4 1-1 1A17 17 0 0 1 3 4c0-.6.4-1 1-1h3.5c.6 0 1 .4 1 1 0 1.3.2 2.5.6 3.6.1.3 0 .7-.2 1z"/></svg>
        954-218-4063
      </li>
      <li>
        <svg viewBox="0 0 24 24" aria-hidden="true"><path d="M6 2h10l2 2v5H6zM3 10h18a1 1 0 0 1 1 1v7H2v-7a1 1 0 0 1 1-1zm3 10h12v2H6z"/></svg>
        954-582-7341
      </li>
      <li>
        <svg viewBox="0 0 24 24" aria-hidden="true"><path d="M2 5h20v14H2zm2 2v.4l8 5.6 8-5.6V7zm0 2.8V17h16V9.8l-8 5.6z"/></svg>
        info@myrvbonecare.example
      </li>
      <li>
        <svg viewBox="0 0 24 24" aria-hidden="true"><path d="M12 2a10 10 0 1 0 0 20 10 10 0 0 0 0-20zm-1 17.9A8 8 0 0 1 4.2 10L9 15v1a2 2 0 0 0 2 2zm6.9-2.5A2 2 0 0 0 16 16h-1v-3a1 1 0 0 0-1-1H8v-2h2a1 1 0 0 0 1-1V7h2a2 2 0 0 0 2-2v-.4a8 8 0 0 1 2.9 12.8z"/></svg>
        www.myrvbonecare.example
      </li>
    </ul>
  </section>

  <section class="card card-back">
    <div class="practice-mark">
      <span class="dot"></span>
      <span class="practice-name">RV Bone &amp; Vitality Center</span>
    </div>
    <p class="slogan">STEADY HANDS. CENTERED ON YOU</p>
  </section>

</div>
</body>
</html>
```